Website design for legal tech start up in Switzerland (B2B)

We are for a legal tech start up in Switzerland called KOVA. We have been running since August 2016. This will be our first live website.

We need a website designed and business card design for our start-up in Switzerland. We also need the Web design to be converted into HTML and CSS files.

Function of website:
• To inform potential customers of our services
• Form a key part of our digital marketing and sales footprint.
• Branding

Please find attached logo.
Updates

Project Deadline Extended Reason: Giving us time to review submissions and provide opportunity for more submissions. Added Thursday, February 16, 2017

Project Deadline Extended
Reason: Looking for more idea's not necessarily set on blue and grey colours only.

Target Market(s)

B2B tech powered legal services.

Industry/Entity Type

Legal

Contact Information for Business Card

Lean and slick design.

Coding

Coded - Design and coding required

Number of Pages Required

5+ page

Requirements
Must have
• VERY LEAN AND CLEAN DESIGN!
• We have received many great standard designs, but we are looking for something more out-of-the box: You can get inspiration from these designs: http://www.pixelvane.com/websites/clean/
• Thanks!!
• Easy content management system
• Well structured coding for additional development
• Responsive webpage for all types of devices
• SEO optimized
• Tabs (Home, services, team, careers, blog, contact us)
• Colour scheme complementary to logo
Nice to have
• Look and Design - Approachable, High-tech, Modern
• Easy to add chat bot capability in future
Should not have
• Too busy/ too much clutter
• Not take to long to load

```html
<!DOCTYPE html>
<html lang="en">
<head>
<meta charset="utf-8">
<title>KOVA – Legal Services</title>
<link href="https://fonts.googleapis.com/css2?family=Open+Sans:wght@400;600;700&display=swap" rel="stylesheet">
<style>
:root{
  --navy:#16386b;
  --ink:#333;
  --muted:#777;
  --band:#f5f5f5;
  --line:#cfcfcf;
  --footer:#4a4a4a;
  --footer-bottom:#424242;
  --footer-text:#ddd;
  --white:#fff;
  --hero-a:#5f8a45;
  --hero-b:#6e9a3e;
}
*{box-sizing:border-box;margin:0;padding:0}
html,body{width:1200px;height:2459px;overflow:hidden}
body{font-family:"Open Sans",Arial,sans-serif;color:var(--ink);background:var(--white);position:relative}
.wrap{position:absolute;left:131px;width:938px}

/* header */
.site-header{position:absolute;top:0;left:0;width:1200px;height:108px;background:var(--white)}
.brand{position:absolute;left:131px;top:26px;font-size:46px;font-weight:700;letter-spacing:4px;color:#3a3a3a;line-height:56px}
.main-nav{position:absolute;right:131px;top:45px;display:flex;gap:31px;font-size:12px;text-transform:uppercase;color:#555}
.main-nav a{color:inherit;text-decoration:none}
.main-nav a.active{color:var(--navy);font-weight:600}

/* hero */
.hero{position:absolute;top:108px;left:0;width:1200px;height:505px;background:linear-gradient(180deg,var(--hero-a),var(--hero-b))}
.hero-arrow{position:absolute;top:236px;width:24px;height:32px;background:rgba(0,0,0,.75);display:flex;align-items:center;justify-content:center}
.hero-arrow.prev{left:0}.hero-arrow.next{right:0}

/* section titles */
.section-title{font-size:24px;font-weight:700;color:var(--navy);text-transform:uppercase;text-align:center;letter-spacing:.5px}
.btn{display:inline-block;border:1px solid var(--line);background:var(--white);color:#555;text-decoration:none}

/* welcome */
.welcome{top:684px;text-align:center}
.welcome p{margin-top:20px;font-size:11.6px;line-height:20.5px;color:#555}
.welcome .btn{margin-top:19px;width:88px;height:36px;line-height:34px;font-size:12px}

/* services */
.services-band{position:absolute;top:944px;left:0;width:1200px;height:407px;background:var(--band)}
.services{top:1016px}
.service-list{display:flex;justify-content:space-between;margin-top:30px}
.service{width:213px;text-align:center}
.service svg{display:block;margin:0 auto;height:42px}
.service h3{margin-top:6px;font-size:21px;font-weight:400;color:var(--navy);text-transform:uppercase;line-height:28px}
.service p{font-size:9.8px;line-height:16.5px;color:#666;margin-top:2px}
.service .btn{margin-top:16px;width:82px;height:37px;line-height:35px;font-size:9.5px;text-transform:uppercase;color:#888}

/* blog */
.blog{top:1426px}
.blog-head{display:flex;justify-content:space-between;align-items:center}
.blog-head h2{font-size:23px;font-weight:700;color:var(--navy)}
.blog-nav{display:flex;gap:10px}
.blog-nav span{width:22px;height:22px;border:1px solid #aaa;display:flex;align-items:center;justify-content:center}
.post-list{display:flex;justify-content:space-between;margin-top:21px}
.post{width:298px}
.post-media{height:181px;position:relative}
.post-media.building{background:linear-gradient(180deg,#767d86,#60666e)}
.post-media.desk{background:linear-gradient(180deg,#d8d6d2,#c4c1bb)}
.post-media.city{background:linear-gradient(180deg,#6a5e5a,#565050)}
.play{position:absolute;left:50%;top:50%;width:40px;height:40px;margin:-20px 0 0 -20px;border-radius:50%;background:var(--white);display:flex;align-items:center;justify-content:center}
.post h3{margin-top:14px;font-size:15px;font-weight:400;line-height:22px;color:#222}
.post p{margin-top:9px;font-size:10.3px;line-height:16.5px;color:#888;text-align:justify}
.post-meta{margin-top:15px;display:flex;gap:22px;font-size:10.5px;color:#666;align-items:center}
.post-meta span{display:flex;align-items:center;gap:5px}

/* team */
.team-band{position:absolute;top:1854px;left:0;width:1200px;height:332px;background:var(--band)}
.team{top:1960px}
.team-list{display:flex;justify-content:space-between;margin-top:22px}
.member{width:440px;display:flex;gap:11px}
.member-photo{width:97px;height:97px;flex:none}
.member-photo.one{background:linear-gradient(180deg,#9ea3a6,#6c7073)}
.member-photo.two{background:linear-gradient(180deg,#c7b9a6,#9c8c78)}
.member h3{font-size:15.5px;font-weight:400;text-transform:uppercase;color:#222;line-height:22px;margin-top:2px}
.member .role{font-size:11px;color:#333;margin-top:2px}
.member p{font-size:10.3px;line-height:16.5px;color:#888;margin-top:10px}
.member p b{color:#222;font-weight:600}

/* footer */
.site-footer{position:absolute;top:2186px;left:0;width:1200px;height:210px;background:var(--footer);color:var(--footer-text)}
.footer-title{font-size:15.5px;font-weight:400;color:var(--white)}
.contact{position:absolute;left:131px;top:42px}
.contact ul{list-style:none;margin-top:10px;width:170px}
.contact li{display:flex;gap:10px;font-size:10.5px;line-height:15px;margin-bottom:8px}
.contact li svg{flex:none;margin-top:2px}
.map{position:absolute;left:331px;top:74px;width:187px;height:102px;background:linear-gradient(135deg,#eaeaea,#d4d4d4)}
.links{position:absolute;left:644px;top:42px}
.link-cols{display:flex;gap:54px;margin-top:10px}
.link-cols ul{list-style:none}
.link-cols li{font-size:10.5px;line-height:22.3px}
.link-cols li::before{content:"•";margin-right:6px}
.social{position:absolute;left:974px;top:42px}
.social-grid{display:grid;grid-template-columns:25px 25px;gap:8px;margin-top:12px;margin-left:12px}
.social-grid span{width:25px;height:25px;border-radius:50%;background:#6f86a8}
.footer-bottom{position:absolute;top:2396px;left:0;width:1200px;height:63px;background:var(--footer-bottom);border-top:1px solid #5a5a5a;text-align:center;font-size:10.5px;color:var(--footer-text);line-height:38px}
</style>
</head>
<body>

<header class="site-header">
  <div class="brand">KOVA</div>
  <nav class="main-nav">
    <a class="active" href="#">Home</a><a href="#">Services</a><a href="#">Team</a><a href="#">Careers</a><a href="#">Blog</a><a href="#">Contact us</a>
  </nav>
</header>

<section class="hero" role="img" aria-label="Slider photo of an alpine valley landscape">
  <span class="hero-arrow prev"><svg width="10" height="18" viewBox="0 0 10 18"><path d="M8 1 1 9l7 8" fill="none" stroke="#fff" stroke-width="1.5"/></svg></span>
  <span class="hero-arrow next"><svg width="10" height="18" viewBox="0 0 10 18"><path d="m2 1 7 8-7 8" fill="none" stroke="#fff" stroke-width="1.5"/></svg></span>
</section>

<section class="wrap welcome">
  <h1 class="section-title">Welcome to KOVA</h1>
  <p>Donec facilisis volutpat lorem, at euismod velit dignissim ac. Class aptent taciti sociosqu ad litora torquent per conubia nostra, per inceptos himenaeos. Nulla consequat ipsum id mi placerat viverra. Sed tempor ex id dui sagittis, at luctus tortor finibus. Vestibulum ante ipsum primis in faucibus orci luctus et ultrices posuere cubilia Curae; Duis varius condimentum tellus, a faucibus lorem vestibulum eu. Duis sit amet tellus nisl. Maecenas nec metus sodales ante sollicitudin auctor in quis velit. Maecenas libero nisi, dignissim eget nibh a, mollis eleifend tellus. Fusce maximus porttitor libero vitae viverra.</p>
  <a class="btn" href="#">Read more</a>
</section>

<div class="services-band"></div>
<section class="wrap services">
  <h2 class="section-title">Our Services</h2>
  <div class="service-list">
    <article class="service">
      <svg viewBox="0 0 44 40" width="44"><circle cx="22" cy="9" r="7" fill="var(--navy)"/><circle cx="8" cy="13" r="5" fill="var(--navy)"/><circle cx="36" cy="13" r="5" fill="var(--navy)"/><path d="M10 40V28a12 12 0 0 1 24 0v12z" fill="var(--navy)"/><path d="M0 34v-7a8 8 0 0 1 9-7v14zM44 34v-7a8 8 0 0 0-9-7v14z" fill="var(--navy)"/></svg>
      <h3>Family Law</h3>
      <p>Duis varius ate condimentum tellus, faucibus lorem vestibulum eu. Duis sit amet tellus nisl. Maecenas nec metus sodales.</p>
      <a class="btn" href="#">Read more</a>
    </article>
    <article class="service">
      <svg viewBox="0 0 48 40" width="48"><path d="M17 8V4h14v4" fill="none" stroke="var(--navy)" stroke-width="3"/><rect x="1" y="8" width="46" height="31" rx="3" fill="var(--navy)"/><rect x="1" y="20" width="46" height="2" fill="#fff"/></svg>
      <h3>Business Law</h3>
      <p>Duis varius ate condimentum tellus, faucibus lorem vestibulum eu. Duis sit amet tellus nisl. Maecenas nec metus sodales.</p>
      <a class="btn" href="#">Read more</a>
    </article>
    <article class="service">
      <svg viewBox="0 0 52 40" width="52"><path d="M10 16 15 4h22l5 12z" fill="none" stroke="var(--navy)" stroke-width="4"/><rect x="2" y="15" width="48" height="16" rx="4" fill="var(--navy)"/><rect x="6" y="28" width="9" height="11" rx="2" fill="var(--navy)"/><rect x="37" y="28" width="9" height="11" rx="2" fill="var(--navy)"/><circle cx="11" cy="23" r="3.5" fill="#fff"/><circle cx="41" cy="23" r="3.5" fill="#fff"/></svg>
      <h3>Vehicle Law</h3>
      <p>Duis varius ate condimentum tellus, faucibus lorem vestibulum eu. Duis sit amet tellus nisl. Maecenas nec metus sodales.</p>
      <a class="btn" href="#">Read more</a>
    </article>
    <article class="service">
      <svg viewBox="0 0 54 40" width="54"><rect x="2" y="5" width="50" height="30" fill="none" stroke="var(--navy)" stroke-width="3"/><rect x="7" y="10" width="40" height="20" fill="var(--navy)"/><circle cx="27" cy="20" r="8" fill="#fff"/><path d="M25 16h3v9" stroke="var(--navy)" stroke-width="2.5" fill="none"/></svg>
      <h3>Debt Law</h3>
      <p>Duis varius ate condimentum tellus, faucibus lorem vestibulum eu. Duis sit amet tellus nisl. Maecenas nec metus sodales.</p>
      <a class="btn" href="#">Read more</a>
    </article>
  </div>
</section>

<section class="wrap blog">
  <div class="blog-head">
    <h2>BLOG</h2>
    <div class="blog-nav">
      <span><svg width="8" height="10" viewBox="0 0 8 10"><path d="M6 1 2 5l4 4" fill="none" stroke="#555" stroke-width="1.3"/></svg></span>
      <span><svg width="8" height="10" viewBox="0 0 8 10"><path d="m2 1 4 4-4 4" fill="none" stroke="#555" stroke-width="1.3"/></svg></span>
    </div>
  </div>
  <div class="post-list">
    <article class="post">
      <div class="post-media building" role="img" aria-label="Photo of a columned courthouse facade"></div>
      <h3>Donec scelerisque felis at ante rhoncus, non mattis nulla facilisis</h3>
      <p>Integer gravida risus risus, in imperdiet leo convallis sed. Aenean lobortis neque, vitae faucibus lorem. Nulla dignissim tempus nisi, sed lobortis velit faucibus at. Fusce vel rutrum erat. Vivamus blandit interdum egestas.</p>
      <div class="post-meta">
        <span><svg width="10" height="9" viewBox="0 0 10 9"><path d="M5 9 1 5a2.3 2.3 0 0 1 4-3 2.3 2.3 0 0 1 4 3z" fill="#555"/></svg>(28)</span>
        <span><svg width="10" height="10" viewBox="0 0 10 10"><path d="M0 4h2v6H0zM3 4l2-4c1 0 1.5.6 1.2 2L6 4h3.2c.6 0 1 .6.8 1.2L9 9.4c-.1.4-.5.6-.9.6H3z" fill="#555"/></svg>(21)</span>
        <span><svg width="10" height="10" viewBox="0 0 10 10"><rect x=".5" y="1.5" width="9" height="8" fill="none" stroke="#555"/><path d="M.5 4h9" stroke="#555"/></svg>8 Feb, 2017</span>
      </div>
    </article>
    <article class="post">
      <div class="post-media desk" role="img" aria-label="Photo of a document being stamped on a desk"></div>
      <h3>Donec scelerisque felis at ante rhoncus, non mattis nulla facilisis</h3>
      <p>Integer gravida risus risus, in imperdiet leo convallis sed. Aenean lobortis neque, vitae faucibus lorem. Nulla dignissim tempus nisi, sed lobortis velit faucibus at. Fusce vel rutrum erat. Vivamus blandit interdum egestas.</p>
      <div class="post-meta">
        <span><svg width="10" height="9" viewBox="0 0 10 9"><path d="M5 9 1 5a2.3 2.3 0 0 1 4-3 2.3 2.3 0 0 1 4 3z" fill="#555"/></svg>(28)</span>
        <span><svg width="10" height="10" viewBox="0 0 10 10"><path d="M0 4h2v6H0zM3 4l2-4c1 0 1.5.6 1.2 2L6 4h3.2c.6 0 1 .6.8 1.2L9 9.4c-.1.4-.5.6-.9.6H3z" fill="#555"/></svg>(21)</span>
        <span><svg width="10" height="10" viewBox="0 0 10 10"><rect x=".5" y="1.5" width="9" height="8" fill="none" stroke="#555"/><path d="M.5 4h9" stroke="#555"/></svg>8 Feb, 2017</span>
      </div>
    </article>
    <article class="post">
      <div class="post-media city" role="img" aria-label="Video still of an old riverside town">
        <span class="play"><svg width="14" height="16" viewBox="0 0 14 16"><path d="M2 1l11 7-11 7z" fill="#222"/></svg></span>
      </div>
      <h3>Donec scelerisque felis at ante rhoncus, non mattis nulla facilisis</h3>
      <p>Integer gravida risus risus, in imperdiet leo convallis sed. Aenean lobortis neque, vitae faucibus lorem. Nulla dignissim tempus nisi, sed lobortis velit faucibus at. Fusce vel rutrum erat. Vivamus blandit interdum egestas.</p>
      <div class="post-meta">
        <span><svg width="10" height="9" viewBox="0 0 10 9"><path d="M5 9 1 5a2.3 2.3 0 0 1 4-3 2.3 2.3 0 0 1 4 3z" fill="#555"/></svg>(28)</span>
        <span><svg width="10" height="10" viewBox="0 0 10 10"><path d="M0 4h2v6H0zM3 4l2-4c1 0 1.5.6 1.2 2L6 4h3.2c.6 0 1 .6.8 1.2L9 9.4c-.1.4-.5.6-.9.6H3z" fill="#555"/></svg>(21)</span>
        <span><svg width="10" height="10" viewBox="0 0 10 10"><rect x=".5" y="1.5" width="9" height="8" fill="none" stroke="#555"/><path d="M.5 4h9" stroke="#555"/></svg>8 Feb, 2017</span>
      </div>
    </article>
  </div>
</section>

<div class="team-band"></div>
<section class="wrap team">
  <h2 class="section-title">Our Team</h2>
  <div class="team-list">
    <article class="member">
      <div class="member-photo one" role="img" aria-label="Portrait photo of team member Marco Keller"></div>
      <div>
        <h3>Marco Keller</h3>
        <div class="role">Duis sed congue nibh</div>
        <p>Aenean lobortis neque, vitae faucibus lorem. Nulla dignissim tempus nisi, sed lobortis velit faucibus at. Fusce vel rutrum erat. Vivamus blandit interdum egestas. <b>More</b></p>
      </div>
    </article>
    <article class="member">
      <div class="member-photo two" role="img" aria-label="Portrait photo of team member Lena"></div>
      <div>
        <h3>Lena</h3>
        <div class="role">Duis sed congue nibh</div>
        <p>Aenean lobortis neque, vitae faucibus lorem. Nulla dignissim tempus nisi, sed lobortis velit faucibus at. Fusce vel rutrum erat. Vivamus blandit interdum egestas. <b>More</b></p>
      </div>
    </article>
  </div>
</section>

<footer class="site-footer">
  <div class="contact">
    <h4 class="footer-title">Contact info</h4>
    <ul>
      <li><svg width="8" height="11" viewBox="0 0 8 11"><path d="M4 11 .6 5.5A3.6 3.6 0 1 1 7.4 5.5z" fill="#ddd"/><circle cx="4" cy="4" r="1.3" fill="#4a4a4a"/></svg>24 Building name, Street name City - Zipcode</li>
      <li><svg width="8" height="11" viewBox="0 0 8 11"><rect x=".5" y=".5" width="7" height="10" rx="1" fill="#ddd"/><rect x="1.8" y="2" width="4.4" height="6" fill="#4a4a4a"/></svg>555 018 2047</li>
      <li><svg width="8" height="11" viewBox="0 0 8 11"><rect x=".5" y=".5" width="7" height="10" rx="1" fill="#ddd"/><rect x="1.8" y="2" width="4.4" height="6" fill="#4a4a4a"/></svg>555 019 3316</li>
      <li><svg width="9" height="8" viewBox="0 0 9 8"><rect width="9" height="7" y=".5" fill="#ddd"/><path d="M0 1l4.5 3.5L9 1" fill="none" stroke="#4a4a4a"/></svg>info@kova-legal.ch</li>
    </ul>
  </div>
  <div class="map" role="img" aria-label="Small street map showing the office location"></div>
  <div class="links">
    <h4 class="footer-title">Links</h4>
    <div class="link-cols">
      <ul><li>Home</li><li>Services</li><li>Team</li><li>Careers</li><li>Blog</li></ul>
      <ul><li>Contact us</li><li>Terms and conditions</li><li>Privacy Policy</li><li>Sitemap</li></ul>
    </div>
  </div>
  <div class="social">
    <h4 class="footer-title">Social Media</h4>
    <div class="social-grid"><span></span><span></span><span></span><span></span></div>
  </div>
</footer>
<div class="footer-bottom">Copyright &copy; 2017 Company name. All rights reserved.</div>

</body>
</html>
```